Request for Business Card Design

Hi. My name is Marlene, I am looking for a new business card design for my company, Quarrow Signal Instruments, LLC. I really like the design you did for Tarsel Venture and was hoping you could do something similar using our full logo and our mark. I am also open to any raised texture design using our mark. I have attached our full logo, which would need to be somewhere on the card, as well as the mark in both outline and full form, as well as our brand colors / guide. The card does not have to be white, as long as our logo and mark appear. I actually like darker colored business cards more, but am open to all options. If you are interested in working with me, please let me know. We would also take the business card design into letterhead design if you can do that.

```html
<!DOCTYPE html>
<html lang="en">
<head>
<meta charset="utf-8">
<title>Quarrow Signal Instruments – Business Card</title>
<link rel="stylesheet" href="https://fonts.googleapis.com/css2?family=Montserrat:wght@400;500;700&display=swap">
<style>
  :root {
    --brand-blue: #0b9ac1;
    --ink-grey: #474849;
    --ink-dark: #1f1f1f;
    --card-white: #ffffff;
    --backdrop: #2a2a2a;
  }
  * { margin: 0; padding: 0; box-sizing: border-box; }
  html, body { width: 1200px; height: 880px; overflow: hidden; }
  body {
    background: var(--backdrop);
    font-family: "Montserrat", sans-serif;
    position: relative;
  }
  .card {
    position: absolute;
    width: 540px;
    height: 309px;
    overflow: hidden;
    box-shadow: 0 10px 30px rgba(0,0,0,.45);
  }
  .card--front { left: 50px; top: 100px; background: var(--brand-blue); }
  .card--back  { left: 610px; top: 470px; background: var(--card-white); }

  .brand { display: flex; align-items: center; gap: 14px; position: absolute; }
  .brand__dot { width: 58px; height: 58px; border-radius: 50%; flex: none; }
  .brand__name { font-weight: 700; line-height: 1; }
  .brand__name span { display: block; }
  .brand__line1 { letter-spacing: 4px; }
  .brand__line2 { letter-spacing: 1.2px; margin-top: 5px; }

  .card--front .brand { left: 105px; top: 118px; color: var(--card-white); }
  .card--front .brand__dot { background: var(--card-white); }
  .card--front .brand__line1 { font-size: 44px; }
  .card--front .brand__line2 { font-size: 15px; }

  .card--back .brand { left: 215px; top: 40px; color: var(--ink-grey); gap: 10px; }
  .card--back .brand__dot { width: 38px; height: 38px; background: var(--brand-blue); }
  .card--back .brand__line1 { font-size: 29px; }
  .card--back .brand__line2 { font-size: 10px; margin-top: 3px; }

  .person { position: absolute; left: 34px; top: 140px; }
  .person__name { font-size: 17px; font-weight: 700; color: var(--ink-grey); letter-spacing: .3px; }
  .person__name .first { color: var(--brand-blue); }
  .person__role { font-size: 14px; font-weight: 400; color: var(--ink-dark); margin-top: 3px; }

  .address {
    position: absolute; right: 30px; top: 140px;
    text-align: right; font-size: 13.5px; line-height: 1.35; color: var(--ink-dark);
  }

  .contacts { position: absolute; left: 34px; top: 188px; list-style: none; }
  .contacts li {
    display: flex; align-items: center; gap: 8px;
    font-size: 13.5px; color: var(--ink-dark); margin-bottom: 4px;
  }
  .contacts svg { width: 13px; height: 13px; flex: none; fill: var(--brand-blue); }

  .bands { position: absolute; left: 0; bottom: 0; width: 540px; height: 309px; }
</style>
</head>
<body>

<section class="card card--front" aria-label="Card front">
  <div class="brand">
    <div class="brand__dot"></div>
    <div class="brand__name">
      <span class="brand__line1">QUARROW</span>
      <span class="brand__line2">SIGNAL INSTRUMENTS</span>
    </div>
  </div>
</section>

<section class="card card--back" aria-label="Card back">
  <svg class="bands" viewBox="0 0 540 309" aria-hidden="true">
    <polygon points="0,290 540,290 540,309 0,309" fill="var(--brand-blue)"/>
    <polygon points="410,228 540,228 540,309 400,309 400,246" fill="var(--brand-blue)"/>
    <polygon points="0,276 140,276 140,284 0,284" fill="var(--ink-grey)"/>
    <polygon points="146,276 300,276 300,284 146,284" fill="var(--brand-blue)"/>
    <polygon points="306,276 388,276 398,258 404,258 392,284 306,284" fill="var(--ink-grey)"/>
  </svg>

  <div class="brand">
    <div class="brand__dot"></div>
    <div class="brand__name">
      <span class="brand__line1">QUARROW</span>
      <span class="brand__line2">SIGNAL INSTRUMENTS</span>
    </div>
  </div>

  <div class="person">
    <p class="person__name"><span class="first">RHEA</span> CALLOWAY</p>
    <p class="person__role">Owner</p>
  </div>

  <p class="address">48 Fenwick Row, Ste<br>200, Arlow, TX 75010</p>

  <ul class="contacts">
    <li>
      <svg viewBox="0 0 24 24"><path d="M6.6 10.8a15 15 0 0 0 6.6 6.6l2.2-2.2a1 1 0 0 1 1-.25 11.4 11.4 0 0 0 3.6.6 1 1 0 0 1 1 1V20a1 1 0 0 1-1 1A17 17 0 0 1 3 4a1 1 0 0 1 1-1h3.5a1 1 0 0 1 1 1c0 1.25.2 2.45.6 3.6a1 1 0 0 1-.25 1z"/></svg>
      555.210.4417
    </li>
    <li>
      <svg viewBox="0 0 24 24"><path d="M2 5h20v14H2zM3.5 6.5 12 13l8.5-6.5z" fill-rule="evenodd"/></svg>
      info@quarrowsignal.com
    </li>
    <li>
      <svg viewBox="0 0 24 24"><circle cx="12" cy="12" r="10"/></svg>
      www.quarrowsignal.com
    </li>
  </ul>
</section>

</body>
</html>
```